Design a web site for my business - Brightline Coatings Co.

We are a family business that handles design, fabrication and installation of powder coated aluminum, stainless steel and glass products. Including handrails, privacy slat screens, electric gates and pool fencing. We are based in the Whitsundays in North Queensland and service an area from Airlie Beach to Townsville.

Target Market(s)

Domestic and commercial

Industry/Entity Type

fabrication - manufacturing

Coding

Coded - Design and coding required

Number of Pages Required

5+ page

Colors
0054AA
0677BA
7BADD7
CADEEF
E8F1F8

Requirements
Must have
• photo galleries, contact page, one page for privacy screens, balustrades, glass fencing, stainless steel handrail, powder coated aluminium handrails and pool fencing

```html
<!DOCTYPE html>
<html lang="en">
<head>
<meta charset="utf-8">
<title>Brightline Coatings Co — Fabrication &amp; Installation across the Whitsundays</title>
<link href="https://fonts.googleapis.com/css2?family=Inter:ital,wght@0,300;0,400;0,500;0,600;0,800;1,800&family=Audiowide&family=Poppins:wght@400;500&display=swap" rel="stylesheet">
<style>
:root{
  --blue-deep:#0054AA;
  --blue:#0677BA;
  --blue-soft:#7BADD7;
  --blue-pale:#CADEEF;
  --blue-mist:#E8F1F8;
  --ink:#1f2a38;
  --muted:#6f7d8c;
  --white:#ffffff;
}
*{margin:0;padding:0;box-sizing:border-box}
html,body{width:1200px;height:3650px;overflow:hidden;background:var(--white)}
body{position:relative;font-family:"Inter",sans-serif;color:var(--ink)}
.abs{position:absolute}
.rule{position:absolute;background:var(--blue-pale);height:1px}
.vrule{position:absolute;background:var(--blue-pale);width:1px}

/* hero */
.hero{position:absolute;left:0;top:0;width:1200px;height:708px;
  background:linear-gradient(180deg,#3d4a5c 0%,#4f6270 25%,#2f4030 50%,#3a3530 75%,#2a2a30 100%)}
.nav{position:absolute;left:92px;top:37px;width:1013px;height:46px;background:var(--white);border-radius:23px}
.nav-links{position:absolute;left:32px;top:0;height:46px;display:flex;align-items:center;gap:16px;font-size:11px;color:var(--ink)}
.nav-cta{position:absolute;right:6px;top:7px;height:32px;padding:0 24px;background:var(--blue);color:var(--white);
  border-radius:16px;font-size:12px;font-weight:500;display:flex;align-items:center}
.nav-brand{position:absolute;left:553px;top:13px;width:94px;height:94px;border-radius:50%;background:var(--white);
  border:3px solid var(--blue-pale);display:flex;align-items:center;justify-content:center;text-align:center;
  font-size:10px;font-weight:600;color:var(--blue-deep);line-height:1.2}
.hero-title{position:absolute;left:0;width:1200px;top:432px;text-align:center;color:var(--white);font-size:44px;line-height:51px;font-weight:300;letter-spacing:-0.5px}
.hero-title em{font-weight:800;font-style:italic}
.hero-sub{position:absolute;left:0;width:1200px;top:597px;text-align:center;color:var(--white);font-size:12px;line-height:19px}
.scroll-btn{position:absolute;left:573px;top:681px;width:54px;height:54px;border-radius:50%;background:var(--white);border:2px solid var(--blue-pale);display:flex;align-items:center;justify-content:center}

/* who */
.h2{font-size:36px;font-weight:300;color:var(--blue-deep);letter-spacing:-0.5px}
.h2 em{font-weight:800;font-style:italic}
.body-text{font-size:11px;line-height:17px;color:var(--muted)}
.btn{position:absolute;height:32px;border-radius:16px;font-size:11px;font-weight:500;display:flex;align-items:center;justify-content:center}
.btn-fill{background:var(--blue);color:var(--white)}
.btn-line{border:1px solid var(--blue-deep);color:var(--blue-deep);background:var(--white)}
.ghost{position:absolute;font-weight:800;color:var(--blue-mist);letter-spacing:-3px;white-space:nowrap}
.brand-disc{position:absolute;left:760px;top:790px;width:290px;height:290px;border-radius:50%;background:var(--blue-soft);
  display:flex;align-items:center;justify-content:center;color:var(--white);font-size:30px;font-weight:600}

/* offer */
.card{position:absolute;top:1369px;width:305px;height:283px;background:var(--blue-mist);border-radius:14px}
.card-num{position:absolute;left:26px;top:24px;width:50px;height:50px;border-radius:50%;background:var(--blue);color:var(--white);
  font-size:19px;display:flex;align-items:center;justify-content:center}
.card-title{position:absolute;left:26px;top:138px;font-size:17px;font-weight:500;color:var(--blue-deep);letter-spacing:-0.3px}
.card-text{position:absolute;left:26px;top:168px;width:255px;font-size:10px;line-height:17px;color:var(--muted)}
.card-arrow{position:absolute;left:26px;top:229px;width:29px;height:29px;border-radius:5px;background:var(--blue);display:flex;align-items:center;justify-content:center}

/* projects */
.photo{position:absolute;border-radius:10px;overflow:hidden}
.photo-caption{position:absolute;left:24px;bottom:22px;color:var(--white)}
.photo-caption .place{font-size:10px;margin-bottom:6px}
.photo-caption .name{font-size:14px;font-weight:600;line-height:18px}
.photo-arrow{position:absolute;right:24px;bottom:34px;width:30px;height:30px;border-radius:5px;background:var(--blue);display:flex;align-items:center;justify-content:center}

/* cta */
.cta{position:absolute;left:125px;top:2557px;width:949px;height:546px;border-radius:20px;
  background:linear-gradient(160deg,#8c9298 0%,#5f5a55 45%,#3a2c24 75%,#2b2b2e 100%)}
.cta-title{position:absolute;left:61px;top:308px;font-family:"Audiowide",sans-serif;font-size:32px;line-height:38px;color:var(--white);letter-spacing:2px}
.cta-sub{position:absolute;left:61px;top:392px;font-family:"Poppins",sans-serif;font-size:11px;line-height:17px;color:var(--white)}
.btn-white{background:var(--white);color:var(--ink);font-weight:600}
.btn-outline-white{border:1px solid var(--white);color:var(--white);font-weight:600}

/* footer */
.foot-brand{position:absolute;left:125px;top:3300px;font-size:22px;font-weight:600;color:var(--blue-deep);line-height:28px}
.foot-head{position:absolute;top:3250px;font-size:18px;font-weight:500;color:var(--blue-deep)}
.foot-list{position:absolute;top:3288px;list-style:none;font-size:11px;line-height:24px;color:var(--muted)}
.contact-row{position:absolute;left:843px;display:flex;align-items:center;gap:9px;font-size:11px;color:var(--muted)}
.contact-ico{width:21px;height:21px;border-radius:50%;background:var(--blue);display:flex;align-items:center;justify-content:center}
.copyright{position:absolute;left:0;width:1200px;top:3613px;text-align:center;font-size:10px;color:var(--muted)}
</style>
</head>
<body>

<section class="hero">
  <div class="abs" role="img" aria-label="Photo of a timber boardwalk with railings along the Airlie Beach waterfront, palms and hills behind" style="inset:0;background:linear-gradient(180deg,rgba(40,50,65,0) 0%,rgba(20,22,28,.35) 100%)"></div>
  <nav class="nav">
    <div class="nav-links"><span>Home</span><span>About Us</span><span>Services</span><span>Projects</span><span>Contact</span></div>
    <div class="nav-cta">REQUEST A QUOTE</div>
  </nav>
  <div class="nav-brand">Brightline<br>Coatings Co</div>
  <h1 class="hero-title">EXPERT FABRICATION &amp;<br><em>INSTALLATION ACROSS</em><br>THE&nbsp; WHITSUNDAYS</h1>
  <p class="hero-sub">Design, fabrication and installation across the Whitsundays — from<br>Airlie Beach to Townsville.</p>
</section>

<div class="rule" style="left:18px;top:720px;width:540px"></div>
<div class="rule" style="left:642px;top:720px;width:540px"></div>
<div class="scroll-btn"><svg width="22" height="14" viewBox="0 0 22 14"><path d="M2 2l9 9 9-9M6 2l5 5 5-5" fill="none" stroke="#0054AA" stroke-width="1.5"/></svg></div>
<div class="vrule" style="left:18px;top:740px;height:1385px"></div>
<div class="vrule" style="left:1181px;top:740px;height:1385px"></div>

<section class="who">
  <div class="ghost" style="left:35px;top:1085px;font-size:112px">BRIGHTLINE</div>
  <div class="brand-disc">Brightline</div>
  <h2 class="h2 abs" style="left:122px;top:812px">WHO <em>WE ARE</em></h2>
  <p class="body-text abs" style="left:122px;top:877px;width:410px">Lorem ipsum dolor sit amet consectetur. Metus diam mauris risus egestas quam sed cursus est ac. Molestie tincidunt volutpat turpis non id mi lorem nulla. Interdum tellus convallis nulla sed aenean. Amet fermentum sit adipiscing sed eget nunc est. Tempor nunc ut sed aenean volutpat. Dui aliquam donec porta at viverra mauris eget sit fringilla.</p>
  <div class="btn btn-fill" style="left:122px;top:987px;width:190px">LEARN MORE ABOUT US</div>
  <div class="btn btn-line" style="left:327px;top:987px;width:162px">REQUEST A QUOTE</div>
</section>
<div class="rule" style="left:35px;top:1210px;width:1130px"></div>

<section class="offer">
  <h2 class="h2 abs" style="left:0;width:1200px;text-align:center;top:1282px">WHAT <em>WE OFFER</em></h2>
  <div class="card" style="left:125px">
    <div class="card-num">01</div><div class="card-title">PRIVACY SLAT SCREENS</div>
    <p class="card-text">Lorem ipsum dolor sit amet consectetur. Gravida facilisi nulla phasellus nullam orci eu ut. Auctor facilisis lectus enim ipsum.</p>
    <div class="card-arrow"><svg width="12" height="10" viewBox="0 0 12 10"><path d="M1 5h10M7 1l4 4-4 4" fill="none" stroke="#fff" stroke-width="1.3"/></svg></div>
  </div>
  <div class="card" style="left:447px">
    <div class="card-num">02</div><div class="card-title">BALUSTRADES</div>
    <p class="card-text">Lorem ipsum dolor sit amet consectetur. Gravida facilisi nulla phasellus nullam orci eu ut. Auctor facilisis lectus enim ipsum.</p>
    <div class="card-arrow"><svg width="12" height="10" viewBox="0 0 12 10"><path d="M1 5h10M7 1l4 4-4 4" fill="none" stroke="#fff" stroke-width="1.3"/></svg></div>
  </div>
  <div class="card" style="left:769px">
    <div class="card-num">03</div><div class="card-title">GLASS POOL FENCING</div>
    <p class="card-text">Lorem ipsum dolor sit amet consectetur. Gravida facilisi nulla phasellus nullam orci eu ut. Auctor facilisis lectus enim ipsum.</p>
    <div class="card-arrow"><svg width="12" height="10" viewBox="0 0 12 10"><path d="M1 5h10M7 1l4 4-4 4" fill="none" stroke="#fff" stroke-width="1.3"/></svg></div>
  </div>
  <div class="btn btn-line" style="left:517px;top:1685px;width:166px">VIEW ALL SERVICES</div>
</section>
<div class="rule" style="left:35px;top:1800px;width:1130px"></div>

<section class="projects">
  <h2 class="h2 abs" style="left:0;width:1200px;text-align:center;top:1872px;line-height:44px">FEATURED PROJECTS ACROSS<br><em>THE WHITSUNDAYS.</em></h2>
  <div class="photo" role="img" aria-label="Frameless glass pool fence beside tropical garden and stone paving" style="left:125px;top:2067px;width:305px;height:299px;background:linear-gradient(160deg,#3f5a3a 0%,#7c8a78 55%,#a9aaa4 100%)"></div>
  <div class="photo" role="img" aria-label="Timber deck walkway with stainless steel balustrade and handrails among trees" style="left:447px;top:2005px;width:305px;height:299px;background:linear-gradient(170deg,#4c5a48 0%,#6a5f55 50%,#2f2b2a 100%)">
    <div class="photo-caption"><div class="place">Airlie Beach</div><div class="name">RESIDENTIAL BALUSTRADE<br>&amp; HANDRAILS</div></div>
    <div class="photo-arrow"><svg width="12" height="10" viewBox="0 0 12 10"><path d="M1 5h10M7 1l4 4-4 4" fill="none" stroke="#fff" stroke-width="1.3"/></svg></div>
  </div>
  <div class="photo" role="img" aria-label="Cream aluminium slat gates and screen under a blue sky" style="left:769px;top:2067px;width:305px;height:299px;background:linear-gradient(180deg,#1f3f7a 0%,#5a7aa8 38%,#cfc9bd 60%,#b9b8b4 100%)"></div>
</section>
<div class="rule" style="left:35px;top:2475px;width:1130px"></div>

<section class="cta" role="img" aria-label="Photo of a timber roofed deck with white metal balustrade against an overcast sky">
  <h2 class="cta-title">READY TO START<br>YOUR PROJECT?</h2>
  <p class="cta-sub">Get expert advice and a free, no-obligation quote from the Whitsundays'<br>trusted powder coating and metal fabrication team.</p>
  <div class="btn btn-white" style="left:61px;top:444px;width:162px">REQUEST A QUOTE</div>
  <div class="btn btn-outline-white" style="left:242px;top:444px;width:114px">CALL NOW</div>
</section>
<div class="rule" style="left:35px;top:3185px;width:1130px"></div>

<footer>
  <div class="foot-brand">Brightline<br>Coatings Co</div>
  <div class="vrule" style="left:357px;top:3252px;height:160px"></div>
  <div class="vrule" style="left:570px;top:3252px;height:160px"></div>
  <div class="vrule" style="left:796px;top:3252px;height:160px"></div>

  <div class="foot-head" style="left:405px">QUICK LINKS</div>
  <ul class="foot-list" style="left:405px"><li>Home</li><li>About Us</li><li>Services</li><li>Projects</li><li>Contact</li></ul>

  <div class="foot-head" style="left:618px">SERVICE AREA</div>
  <ul class="foot-list" style="left:618px"><li>Airlie Beach</li><li>Cannonvale</li><li>Proserpine</li><li>Bowen</li><li>Mackay</li><li>Townsville</li></ul>

  <div class="foot-head" style="left:843px">CONTACT</div>
  <div class="contact-row" style="top:3290px"><span class="contact-ico"><svg width="10" height="10" viewBox="0 0 10 10"><path d="M2 1l2 2-1 1.5a6 6 0 002.5 2.5L7 6l2 2-1.5 1.5C4 9 1 6 .5 2.5z" fill="#fff"/></svg></span>0400 000 000</div>
  <div class="contact-row" style="top:3321px"><span class="contact-ico"><svg width="11" height="8" viewBox="0 0 11 8"><rect x=".5" y=".5" width="10" height="7" fill="none" stroke="#fff"/><path d="M.5 .5l5 4 5-4" fill="none" stroke="#fff"/></svg></span>info@brightlinecoatings.com.au</div>
  <div class="contact-row" style="top:3351px"><span class="contact-ico"><svg width="8" height="11" viewBox="0 0 8 11"><path d="M4 10.5S.5 6.5.5 4a3.5 3.5 0 017 0c0 2.5-3.5 6.5-3.5 6.5z" fill="none" stroke="#fff"/><circle cx="4" cy="4" r="1.2" fill="#fff"/></svg></span>Airlie Beach, QLD</div>

  <div class="ghost" style="left:-200px;top:3455px;font-size:120px">BRIGHTLINE</div>
  <div class="abs" style="left:550px;top:3465px;width:100px;height:100px;border-radius:50%;background:var(--blue-soft)"></div>
  <div class="ghost" style="left:670px;top:3455px;font-size:120px">BRIGHTLINE</div>

  <div class="rule" style="left:125px;top:3596px;width:949px"></div>
  <p class="copyright">© 2026 Brightline Coatings Co. All rights reserved.</p>
</footer>

</body>
</html>
```